Development of musical artist Tavro Quill's Website

I need a website designed for a reggae musical artist by the name of Tavro Quill. The site should be representative of a Reggae artist from Jamaica that has a Caribbean appeal but also attractive to global audiences. The website should be responsive for all devices (desktop, laptop, mobile). It should be optimized for SEO purposes. Icons for Photoshare, Friendbook, Chirper, VideoHub should be included. The sections of the website should be as follows: Home, Media, News, Bio, Join, Contact. The 'Join' section should be a form for database collection to the fan club. I would like to easily be able to dump this database in an excel or .csv file at any given time. The 'Media' section should be able to showcase video thumbnails and allow persons to play videos through the site and the videos will be fed from VideoHub. The 'News' section will be for announcements and or new releases where the artist is mentioned. The site should also be built in such a way that analytics can be easily implemented. This website should be the main call to action for this artist moving forward. I would also like the website to have a easy to use CMS platform (Wordpress perhaps). The URL for the website will be tavroquillstar.example. Here are the links for some of the social media pages:
VideoHub - https://www.videohub.example/user/TavroQuill
Photoshare - https://www.photoshare.example/tavroquill/
A good website to refer to from a design perspective is https://marvello.example/

Target Market(s)

Reggae and Pop music fans

Industry/Entity Type

Artists

Coding

Number of Pages Required

5+ page

Font styles to use
Sans Serif

Requirements
Must have
• Great design
Nice to have
• Parallax technology

```html
<!DOCTYPE html>
<html lang="en">
<head>
<meta charset="utf-8">
<title>Tavro Quill — Reggae Artist from Jamaica</title>
<link rel="stylesheet" href="https://fonts.googleapis.com/css2?family=Archivo+Black&family=Kaushan+Script&family=Montserrat:wght@400;500;600;700;800&display=swap">
<style>
:root{
  --red:#e50914;
  --red-deep:#c8050f;
  --maroon:#2a0a0d;
  --ink:#120b0c;
  --dark:#1a1314;
  --white:#ffffff;
  --grey:#6d6d6d;
  --head:"Archivo Black", "Arial Black", sans-serif;
  --script:"Kaushan Script", cursive;
  --body:"Montserrat", Arial, sans-serif;
}
*{box-sizing:border-box;margin:0;padding:0}
html,body{width:1200px;height:3644px;overflow:hidden}
body{position:relative;background:var(--ink);font-family:var(--body);color:var(--white)}
.abs{position:absolute}
a{color:inherit;text-decoration:none}

/* top bar */
.topbar{left:0;top:0;width:1200px;height:44px;background:var(--red);font-size:14px;font-weight:500}
.topbar .social{position:absolute;left:108px;top:13px;display:flex;gap:22px;font-size:12px;font-weight:600}
.topbar .util{position:absolute;right:110px;top:12px;display:flex;gap:70px}
.topbar .util .search{display:flex;align-items:center;gap:8px}

/* nav */
.mainnav{left:0;top:44px;width:1200px;height:83px;background:var(--maroon)}
.brand{position:absolute;left:115px;top:28px;display:flex;align-items:center;gap:10px;font-weight:800;font-size:24px;letter-spacing:1px}
.brand .dot{width:14px;height:14px;border-radius:50%;background:var(--red)}
.menu{position:absolute;right:110px;top:35px;display:flex;gap:62px;font-size:13px;font-weight:500}

/* hero */
.hero{left:0;top:127px;width:1200px;height:850px;background:radial-gradient(ellipse at 70% 30%,#2a1a16 0%,#0d0a0a 60%)}
.hero-photo{left:740px;top:127px;width:460px;height:700px;background:linear-gradient(180deg,#3a2a22 0%,#2b1d17 55%,#120b0a 100%)}
.hero-mark{left:171px;top:268px;width:412px;height:412px;border-radius:50%;border:6px solid #b44de0;box-shadow:0 0 40px #5a7dff,inset 0 0 40px #e04dbb;background:radial-gradient(circle,#1c0e24 0%,#0b0710 70%)}
.hero-name{left:171px;top:380px;width:412px;text-align:center;font-weight:800;font-size:78px;line-height:82px;color:var(--white)}

/* media band */
.band{left:0;width:1200px}
.cards{left:112px;top:778px;display:flex;gap:12px}
.card{width:318px;height:383px;background:var(--white);border-radius:8px;overflow:hidden;position:relative;color:#111;text-align:center}
.card .thumb{height:194px;position:relative}
.card .play{position:absolute;left:50%;top:50%;width:44px;height:44px;margin:-22px 0 0 -22px;border-radius:50%;background:var(--red);display:flex;align-items:center;justify-content:center}
.card h3{font-family:var(--head);font-style:italic;font-size:17px;margin-top:22px;letter-spacing:.3px}
.card p{font-size:12px;line-height:24px;color:var(--grey);margin:12px 28px 0}
.card .share{position:absolute;left:18px;bottom:20px;width:36px;height:36px;border:2px solid var(--red);border-radius:3px;display:flex;align-items:center;justify-content:center}
.card .love{position:absolute;right:18px;bottom:20px;width:36px;height:36px;background:var(--red);border-radius:3px;display:flex;align-items:center;justify-content:center}

/* section titles */
.section-title{left:0;width:1200px;text-align:center;font-family:var(--head);font-style:italic;font-size:40px;letter-spacing:1px}

/* news */
.news-bg{left:0;top:1270px;width:1200px;height:1080px;background:linear-gradient(180deg,#1d1616 0%,#2a2121 45%,#151010 100%)}
.post{background:var(--red);border-radius:6px;padding:30px 28px}
.post .head{display:flex;gap:18px;align-items:flex-start}
.post .avatar{width:74px;height:74px;border-radius:50%;background:linear-gradient(135deg,#5a7180,#2e3a40);border:3px solid #fff;flex:none}
.post h4{font-family:var(--head);font-style:italic;font-size:22px;line-height:28px}
.post .date{font-family:var(--script);font-size:17px;margin-top:8px}
.post p{font-size:13.5px;line-height:24px;margin:22px 0 0 112px}
.post .btn{display:inline-block;margin:22px 0 0 112px;border:2px solid #fff;padding:9px 30px;font-size:15px;font-weight:600}
.photo{border-radius:6px}
.more{left:574px;top:2165px;width:52px;height:52px;border-radius:50%;border:2px solid #fff;display:flex;align-items:center;justify-content:center}

/* bio */
.bio-photo{left:112px;top:2455px;width:371px;height:351px;border:3px solid #fff;border-radius:6px;background:linear-gradient(180deg,#e8e8e8 0%,#bdbdbd 60%,#8a8a8a 100%)}
.bio-text{left:564px;top:2462px;width:530px}
.bio-text h2{font-family:var(--head);font-style:italic;font-size:40px;letter-spacing:.5px}
.bio-text .role{font-size:16px;font-weight:600;margin-top:4px}
.bio-text p{font-size:14px;line-height:27px;margin-top:28px}
.bio-text .btn{display:inline-block;margin-top:40px;border:2px solid #fff;padding:12px 30px;font-size:15px;font-weight:600}

/* join */
.join-bg{left:0;top:2880px;width:1200px;height:580px;background:linear-gradient(180deg,#181212 0%,#241c1b 50%,#120d0d 100%)}
.field{height:46px;border:2px solid #fff;font-family:var(--head);font-style:italic;font-size:12px;padding:14px 14px;letter-spacing:.3px}
.submit{left:902px;top:3220px;width:102px;height:44px;background:var(--red);font-size:15px;font-weight:600;display:flex;align-items:center;justify-content:center}

/* footer */
.foot-social{left:0;top:3482px;width:1200px;display:flex;justify-content:center;gap:12px}
.foot-social span{height:42px;padding:0 14px;border:2px solid #fff;border-radius:21px;display:flex;align-items:center;font-size:12px;font-weight:600}
.foot-social .heart{width:42px;padding:0;justify-content:center}
.foot-menu{left:0;top:3546px;width:1200px;display:flex;justify-content:center;gap:66px;font-size:13px}
.copy{left:0;top:3618px;width:1200px;text-align:center;font-size:12px}
</style>
</head>
<body>

<header class="abs topbar">
  <nav class="social" aria-label="Social links">
    <a href="#">Friendbook</a><a href="#">Chirper</a><a href="#">Photoshare</a><a href="#">VideoHub</a>
  </nav>
  <div class="util">
    <a href="#">Join</a><a href="#">Sign Up</a>
    <a class="search" href="#"><svg width="13" height="13" viewBox="0 0 14 14"><circle cx="6" cy="6" r="4.5" fill="none" stroke="#fff" stroke-width="2"/><line x1="9.5" y1="9.5" x2="13" y2="13" stroke="#fff" stroke-width="2"/></svg>Search</a>
  </div>
</header>

<div class="abs mainnav">
  <a class="brand" href="#"><span>TAVRO QUILL</span><span class="dot"></span></a>
  <nav class="menu"><a href="#">HOME</a><a href="#">MEDIA</a><a href="#">NEWS</a><a href="#">BIO</a><a href="#">CONTACT</a></nav>
</div>

<section class="abs hero"></section>
<div class="abs hero-photo" role="img" aria-label="Portrait of the artist in an open shirt against a dark backdrop"></div>
<div class="abs hero-mark"></div>
<h1 class="abs hero-name">TAVRO<br>QUILL</h1>

<svg class="abs band" style="top:820px" width="1200" height="540" viewBox="0 0 1200 540">
  <polygon points="0,120 1200,10 1200,525 0,455" fill="var(--red)"/>
</svg>

<div class="abs news-bg" role="img" aria-label="Dimmed photo of the artist performing"></div>
<svg class="abs band" style="top:1260px" width="1200" height="100" viewBox="0 0 1200 100">
  <polygon points="0,0 1200,0 1200,85 0,15" fill="var(--red)"/>
</svg>

<div class="abs cards">
  <article class="card">
    <div class="thumb" role="img" aria-label="Music video still: two people talking outdoors" style="background:linear-gradient(135deg,#8a7a68,#3a2e26)">
      <div class="play"><svg width="16" height="18" viewBox="0 0 16 18"><polygon points="2,1 15,9 2,17" fill="#fff"/></svg></div>
    </div>
    <h3>LOREM IPSUM DOLOR</h3>
    <p>Sed ut perspiciatis unde omnis iste natus error sit voluptatem accusantium doloremque laudantium</p>
    <a class="share" href="#" aria-label="Share"><svg width="14" height="14" viewBox="0 0 14 14"><circle cx="11" cy="3" r="2" fill="#e50914"/><circle cx="3" cy="7" r="2" fill="#e50914"/><circle cx="11" cy="11" r="2" fill="#e50914"/><path d="M11 3L3 7L11 11" stroke="#e50914" stroke-width="1.4" fill="none"/></svg></a>
    <a class="love" href="#" aria-label="Like"><svg width="16" height="14" viewBox="0 0 16 14"><path d="M8 13L1.5 6.5A3.6 3.6 0 0 1 8 2.5A3.6 3.6 0 0 1 14.5 6.5Z" fill="#fff"/></svg></a>
  </article>
  <article class="card">
    <div class="thumb" role="img" aria-label="Music video still: singer in a blue top on a street" style="background:linear-gradient(135deg,#6d8a90,#2f3a3c)">
      <div class="play"><svg width="16" height="18" viewBox="0 0 16 18"><polygon points="2,1 15,9 2,17" fill="#fff"/></svg></div>
    </div>
    <h3>LOREM IPSUM DOLOR</h3>
    <p>Sed ut perspiciatis unde omnis iste natus error sit voluptatem accusantium doloremque laudantium</p>
    <a class="share" href="#" aria-label="Share"><svg width="14" height="14" viewBox="0 0 14 14"><circle cx="11" cy="3" r="2" fill="#e50914"/><circle cx="3" cy="7" r="2" fill="#e50914"/><circle cx="11" cy="11" r="2" fill="#e50914"/><path d="M11 3L3 7L11 11" stroke="#e50914" stroke-width="1.4" fill="none"/></svg></a>
    <a class="love" href="#" aria-label="Like"><svg width="16" height="14" viewBox="0 0 16 14"><path d="M8 13L1.5 6.5A3.6 3.6 0 0 1 8 2.5A3.6 3.6 0 0 1 14.5 6.5Z" fill="#fff"/></svg></a>
  </article>
  <article class="card">
    <div class="thumb" role="img" aria-label="Music video still: artist in a cap outdoors" style="background:linear-gradient(135deg,#6f7a4e,#2c2a1e)">
      <div class="play"><svg width="16" height="18" viewBox="0 0 16 18"><polygon points="2,1 15,9 2,17" fill="#fff"/></svg></div>
    </div>
    <h3>LOREM IPSUM DOLOR</h3>
    <p>Sed ut perspiciatis unde omnis iste natus error sit voluptatem accusantium doloremque laudantium</p>
    <a class="share" href="#" aria-label="Share"><svg width="14" height="14" viewBox="0 0 14 14"><circle cx="11" cy="3" r="2" fill="#e50914"/><circle cx="3" cy="7" r="2" fill="#e50914"/><circle cx="11" cy="11" r="2" fill="#e50914"/><path d="M11 3L3 7L11 11" stroke="#e50914" stroke-width="1.4" fill="none"/></svg></a>
    <a class="love" href="#" aria-label="Like"><svg width="16" height="14" viewBox="0 0 16 14"><path d="M8 13L1.5 6.5A3.6 3.6 0 0 1 8 2.5A3.6 3.6 0 0 1 14.5 6.5Z" fill="#fff"/></svg></a>
  </article>
</div>

<h2 class="abs section-title" style="top:1384px">NEWS</h2>

<article class="abs post" style="left:119px;top:1480px;width:362px;height:311px">
  <div class="head"><div class="avatar" role="img" aria-label="Artist avatar"></div><div><h4>SED UT<br>PERSPICIATIS</h4><div class="date">May 5,2019</div></div></div>
  <p style="margin-top:12px">Lorem ipsum dolor sit amet, consectetur adipiscing elit, sed do eiusmod te</p>
  <a class="btn" href="#" style="margin-top:24px;margin-left:92px">Join Us</a>
</article>
<div class="abs photo" role="img" aria-label="Artist in a blue tank top pointing at the camera on a beach" style="left:488px;top:1480px;width:593px;height:311px;background:linear-gradient(180deg,#bfe2f0 0%,#7fc2dc 55%,#3a8fb0 100%)"></div>
<div class="abs photo" role="img" aria-label="Artist in a black cap and t-shirt on a street" style="left:119px;top:1798px;width:595px;height:309px;background:linear-gradient(180deg,#e4e4e4 0%,#a9a9a9 60%,#6a6a6a 100%)"></div>
<article class="abs post" style="left:719px;top:1798px;width:362px;height:309px">
  <div class="head"><div class="avatar" role="img" aria-label="Artist avatar"></div><div><h4>SED UT<br>PERSPICIATIS</h4><div class="date">June 5,2019</div></div></div>
  <p style="margin-top:12px">Lorem ipsum dolor sit amet, consectetur adipiscing elit, sed do eiusmod te</p>
  <a class="btn" href="#" style="margin-top:24px;margin-left:92px">Join Us</a>
</article>
<a class="abs more" href="#" aria-label="More news"><svg width="16" height="14" viewBox="0 0 16 14"><path d="M2 2L7 7L2 12M8 2L13 7L8 12" stroke="#fff" stroke-width="2" fill="none"/></svg></a>

<svg class="abs band" style="top:2270px" width="1200" height="690" viewBox="0 0 1200 690">
  <polygon points="0,65 1200,0 1200,685 0,635" fill="var(--red)"/>
</svg>
<div class="abs bio-photo" role="img" aria-label="Studio portrait of the artist in a white striped jacket"></div>
<div class="abs bio-text">
  <h2>TAVRO QUILL</h2>
  <div class="role">Reggae artist from Jamaica</div>
  <p>Lorem ipsum dolor sit amet, consectetur adipiscing elit, sed do eiusmod tempor incididunt ut labore et dolore magna aliqua. Ut enim ad minim veniam, quis nostrud exercitation ullamco laboris nisi ut aliquip ex ea commodo consequat. Duis aute irure dolor in reprehenderit in voluptate velit esse cillum dolore eu fugiat nulla pariatur</p>
  <a class="btn" href="#">Learn More</a>
</div>

<div class="abs join-bg" role="img" aria-label="Dimmed photo of a recording studio" style="top:2950px;height:500px"></div>
<h2 class="abs section-title" style="top:3014px">JOIN US</h2>
<form>
  <div class="abs field" style="left:194px;top:3097px;width:398px">NAME</div>
  <div class="abs field" style="left:606px;top:3097px;width:398px">PHONE NO</div>
  <div class="abs field" style="left:194px;top:3158px;width:398px">EMAIL ID</div>
  <div class="abs field" style="left:606px;top:3158px;width:398px">COUNTRY<svg style="position:absolute;right:14px;top:18px" width="10" height="6" viewBox="0 0 10 6"><polygon points="0,0 10,0 5,6" fill="#fff"/></svg></div>
  <div class="abs field" style="left:194px;top:3219px;width:694px">SAY SOMETHING...</div>
  <div class="abs submit">Join Now</div>
</form>

<svg class="abs band" style="top:3385px" width="1200" height="259" viewBox="0 0 1200 259">
  <polygon points="0,65 1200,0 1200,259 0,259" fill="var(--red)"/>
</svg>
<footer>
  <div class="abs foot-social">
    <span>Friendbook</span><span>Chirper</span><span>Photoshare</span><span>VideoHub</span>
    <span class="heart"><svg width="16" height="14" viewBox="0 0 16 14"><path d="M8 13L1.5 6.5A3.6 3.6 0 0 1 8 2.5A3.6 3.6 0 0 1 14.5 6.5Z" fill="#fff"/></svg></span>
  </div>
  <nav class="abs foot-menu"><a href="#">HOME</a><a href="#">MEDIA</a><a href="#">NEWS</a><a href="#">BIO</a><a href="#">JOIN</a><a href="#">CONTACT</a></nav>
  <div class="abs copy">© 2019 Tavro Quill - All registered</div>
</footer>

</body>
</html>
```